website re-design - the brickleaf studio

The Brickleaf Studio is an existing website that we built using a new zealand based online CMS tool which is quite flexible and accomodates custom designs. You can check it here: http://www.pagecrafter.example.nz/.

We have a logo already and the content on the website is OK.
The website can be found at www.thebrickleafstudio.example.au

mainly the homepage, but if the design is easily adapted to the other pages then, we will commission the winner to update these pages also.
Updates

Hi there,  I am uploading an image to be used as the main image on the homepage design,  so all submissions have the same image.

Target Market(s)

property developers, architects, builders, home buyers

Industry/Entity Type

Shop

Requirements
Must have
• Must utilise the existing CMS or at least be compatible to upload
Nice to have
• a promotional banner that can be turned off and on and changed as required as we offer different promotions over time.

```html
<!DOCTYPE html>
<html lang="en">
<head>
<meta charset="utf-8">
<title>The Brickleaf Studio – Architectural Scale Models</title>
<link rel="stylesheet" href="https://fonts.googleapis.com/css2?family=Roboto:wght@300;400;500;700;900&family=Oswald:wght@500;700&display=swap">
<style>
:root{
  --side:#2b2b2b;
  --side-dark:#1c1c1c;
  --page:#ebebeb;
  --ink:#333;
  --ink-soft:#555;
  --muted:#9a9a9a;
  --orange:#f07800;
  --orange-light:#ff9a1f;
  --yellow:#ffc600;
  --green:#3fae12;
  --blue:#1a8cf0;
}
*{box-sizing:border-box;margin:0;padding:0}
html,body{width:857px;height:1200px;overflow:hidden}
body{position:relative;background:var(--page);font-family:Roboto,Arial,sans-serif;color:var(--ink)}
.abs{position:absolute}
.sidebar{left:0;top:0;width:255px;height:1137px;background:var(--side)}
.brand{left:272px;top:29px;display:flex;align-items:center;gap:14px}
.brand-mark{width:120px;height:64px;border:3px solid var(--orange)}
.brand-name{font-size:25px;font-weight:400;color:#222;letter-spacing:.5px;line-height:1}
.brand-tag{left:412px;top:74px;font-size:12px;color:var(--orange);letter-spacing:1px}
.side-tab{left:27px;top:118px;width:228px;height:34px;background:linear-gradient(#ff9a2a,#e36f00);border-radius:5px 0 0 5px;color:#3a1a00;font-family:Oswald,sans-serif;font-weight:700;font-size:17px;display:flex;align-items:center;justify-content:center}
.nav{left:255px;top:118px;width:576px;height:34px;background:linear-gradient(#3c3c3c,#262626);border-radius:0 5px 5px 0;display:flex;align-items:center;padding-left:8px;gap:4px}
.nav a{color:#ddd;font-size:10.5px;text-decoration:none;padding:5px 8px;border-radius:3px}
.nav a.active{background:#151515;color:#fff}
.search{left:56px;top:168px;width:187px;height:23px;background:var(--side-dark);border:1px solid #3a3a3a;color:#888;font-size:10px;padding:5px 7px}
.search-btn{left:219px;top:168px;width:24px;height:23px;background:var(--orange-light)}
.intro{left:56px;top:220px;width:187px;text-align:right;font-weight:300;font-size:16px;line-height:21px;letter-spacing:-.3px;color:#9c9c9c}
.rule{left:40px;width:203px;border-top:1px dotted #555}
.promo{left:59px;width:165px;height:95px;border:1px solid #555;display:flex;flex-direction:column;justify-content:center;align-items:center;font-weight:900;line-height:1;overflow:hidden;color:#111}
.promo-a{top:457px;background:linear-gradient(#fff 0 30%,#1e5cb8 70%,#0d3b80)}
.promo-b{top:573px;background:linear-gradient(#f4f8d8 0 30%,#5a9a10 70%,#2f6000)}
.promo .line1{font-size:19px;letter-spacing:-.5px}
.promo .big{font-size:38px;letter-spacing:-1px}
.promo .row{display:flex;align-items:flex-start;gap:6px}
.promo .from{font-size:14px;margin-top:4px}
.promo small{font-size:13px;color:#fff;letter-spacing:.5px}
.side-head{right:614px;font-size:18px;font-weight:300;color:var(--orange)}
.field{left:56px;width:187px;height:23px;background:var(--side-dark);border:1px solid #3a3a3a;color:#999;font-size:10px;padding:5px 4px}
.subscribe{left:162px;top:809px;width:80px;height:25px;background:linear-gradient(#3aa6ff,#0b6fd8);color:#052a55;font-family:Oswald,sans-serif;font-weight:700;font-size:12px;display:flex;align-items:center;justify-content:center}
.map{left:40px;top:914px;width:203px;height:94px;background:linear-gradient(90deg,#e6e0cc 55%,#a9c4e6 70%);border:3px solid #fff}
.address{left:40px;top:1041px;width:203px;text-align:right;font-size:10px;line-height:12px;color:#999}
.address a{color:var(--yellow);text-decoration:none}
.hero{left:272px;top:170px;width:538px;height:301px;border:3px solid #cfcfcf;background:radial-gradient(ellipse at 50% 40%,#6e7a6c,#2f3a2c 75%)}
.hero-cap{left:275px;top:423px;width:532px;height:45px;background:rgba(20,20,20,.7);color:#ddd;font-weight:300;font-size:13.5px;line-height:17px;padding:5px 0 0 17px}
.arrow-btn{top:434px;width:27px;height:27px;border-radius:50%;background:#eee}
h2{position:absolute;font-weight:400;color:var(--ink)}
.lead{left:271px;top:530px;font-size:12.5px;line-height:16px;color:var(--ink-soft)}
.checks{left:310px;top:584px;width:505px;list-style:none}
.checks li{position:relative;padding-left:23px;color:var(--orange);font-size:9.5px;line-height:12.5px;margin-bottom:11px}
.checks svg{position:absolute;left:2px;top:1px}
.step-num{top:804px;width:40px;height:40px;border-radius:50%;background:#d3d3d3;border:2px solid #e9e9e9;box-shadow:0 0 0 1px #bbb;font-weight:700;font-size:20px;display:flex;align-items:center;justify-content:center;color:#333}
.step-text{top:802px;font-size:17px;line-height:21px;color:#444}
.body-copy{left:286px;width:532px;font-size:9.5px;line-height:12px;color:#444}
.cta{top:1011px;width:178px;height:52px;border-radius:3px;font-family:Oswald,sans-serif;font-weight:700;font-size:26px;display:flex;align-items:center;justify-content:center;box-shadow:0 6px 5px -4px rgba(0,0,0,.35)}
.cta-order{left:335px;background:linear-gradient(#3eaaff,#0a6fe0);color:#08305e}
.cta-quote{left:598px;background:linear-gradient(#5fd21f,#2f9a06);color:#123d00}
.or{left:543px;top:1024px;font-family:Oswald,sans-serif;font-weight:700;font-size:21px;color:#555}
.footer{left:0;top:1137px;width:857px;height:63px;background:var(--side)}
.social{top:1152px;width:26px;height:26px;border-radius:4px;background:#cfcfcf;border:2px solid #888}
.copyright{right:26px;top:1159px;font-size:9.5px;color:#999}
</style>
</head>
<body>
<div class="abs sidebar"></div>

<div class="abs brand"><div class="brand-mark"></div><span class="brand-name">THE BRICKLEAF STUDIO</span></div>
<div class="abs brand-tag">ARCHITECTURAL SCALE MODELS</div>

<div class="abs side-tab">THE BRICKLEAF STUDIO</div>
<nav class="abs nav">
  <a class="active" href="#">Home</a><a href="#">Gallery</a><a href="#">Order Online</a><a href="#">Get a Quote</a><a href="#">Contact</a><a href="#">3D Visualitation</a><a href="#">About Us</a><a href="#">Sitemap</a>
</nav>

<div class="abs search">search</div>
<div class="abs search-btn"><svg width="24" height="23" viewBox="0 0 24 23"><circle cx="10" cy="10" r="4.5" fill="none" stroke="#fff" stroke-width="2"/><line x1="13.5" y1="13.5" x2="18" y2="18" stroke="#fff" stroke-width="2.5"/></svg></div>

<p class="abs intro">Getting an architectural model produced can be expensive and time con-suming, but it can also add a lot of value to a project. A scale model lets everyone involved, get a very clear under-standing of your building.</p>

<div class="abs rule" style="top:431px"></div>
<div class="abs promo promo-a"><span class="line1">Affiliates Earn</span><span class="big">20%</span><small>commision</small></div>
<div class="abs promo promo-b"><span class="line1">Hosting plans</span><span class="row"><span class="from">from</span><span class="big">$25</span></span><small>per month</small></div>
<div class="abs rule" style="top:690px"></div>

<div class="abs side-head" style="top:713px">NEWSLETTER</div>
<div class="abs field" style="top:739px">Your name</div>
<div class="abs field" style="top:775px">Email</div>
<div class="abs subscribe">SUBSCRIBE</div>
<div class="abs rule" style="top:865px"></div>

<div class="abs side-head" style="top:878px">CONTACT</div>
<div class="abs map" role="img" aria-label="Street map showing the studio location"></div>
<div class="abs address">
  14 Juniper Lane Unit 6<br>Riverton 40217<br>Block B-233<br><br>
  Phone: 123-456-789<br>Fax: 123-456-789<br>
  Email: <a href="#">hello@brickleaf.example</a><br>
  Website: <a href="#">www.brickleaf.example</a>
</div>

<div class="abs hero" role="img" aria-label="Photo of an architectural scale model of a housing estate"></div>
<div class="abs hero-cap">A scale model lets everyone involved, get a very clear<br>understanding of your building.</div>
<div class="abs arrow-btn" style="left:718px"><svg width="27" height="27"><path d="M16 8l-6 5.5 6 5.5z" fill="#888"/></svg></div>
<div class="abs arrow-btn" style="left:770px"><svg width="27" height="27"><path d="M11 8l6 5.5-6 5.5z" fill="#888"/></svg></div>

<h2 style="left:272px;top:498px;font-size:19.5px">What we do?</h2>
<p class="abs lead">If you answered yes to any of the following questions,<br>then you should be using the brickleaf studio.</p>

<ul class="abs checks">
  <li><svg width="12" height="10"><path d="M1 5l3.5 3.5L11 1" fill="none" stroke="#3fae12" stroke-width="2.5"/></svg>Are you undertaking a new apartment development or land development and need a model for council approval or marketing purposes?</li>
  <li><svg width="12" height="10"><path d="M1 5l3.5 3.5L11 1" fill="none" stroke="#3fae12" stroke-width="2.5"/></svg>Are you getting a new house designed and built and need a clear understanding of how it will look?</li>
  <li><svg width="12" height="10"><path d="M1 5l3.5 3.5L11 1" fill="none" stroke="#3fae12" stroke-width="2.5"/></svg>Are you an architect or building designer looking for a more affordable way to add to your service?</li>
  <li><svg width="12" height="10"><path d="M1 5l3.5 3.5L11 1" fill="none" stroke="#3fae12" stroke-width="2.5"/></svg>Are you wanting to clarify in your own mind how your new building sits on its site?</li>
  <li><svg width="12" height="10"><path d="M1 5l3.5 3.5L11 1" fill="none" stroke="#3fae12" stroke-width="2.5"/></svg>Are you looking to for a way to market your buildings in an effective and affordable format that everyone can relate to?</li>
</ul>

<h2 style="left:275px;top:755px;font-size:20px">It's this easy</h2>
<div class="abs step-num" style="left:286px">1</div>
<div class="abs step-text" style="left:336px;text-align:center">Order online or fill<br>in the quote form</div>
<svg class="abs" style="left:502px;top:806px" width="30" height="34" viewBox="0 0 30 34"><path d="M2 2h11l15 15-15 15H2l15-15z" fill="#4cc21a"/></svg>
<div class="abs step-num" style="left:557px">2</div>
<div class="abs step-text" style="left:603px">We'll build your model and<br>deliver it right to your door</div>

<p class="abs body-copy" style="top:878px">You can tailor your model to suit your project and budget needs. There are various add-ons such as a display case, internal walls, acrylic windows, people trees and cars and site contours as well as a scaled pricing structure based on the size of your building.</p>
<p class="abs body-copy" style="top:926px">We have made the system very easy to use, so all you need to do is click your way to your new scale model. Just follow the prompts and away you go. Click here to order your model now. Or click here to get a quote.</p>

<div class="abs cta cta-order">ORDER NOW</div>
<div class="abs or">OR</div>
<div class="abs cta cta-quote">GET A QUOTE</div>

<div class="abs footer"></div>
<div class="abs social" style="left:255px"></div>
<div class="abs social" style="left:292px"></div>
<div class="abs social" style="left:328px"></div>
<div class="abs social" style="left:365px"></div>
<div class="abs social" style="left:402px"></div>
<div class="abs copyright">2011 © Copyright The Brickleaf Studio - Site map Phone: (08) 5550 0142 Australia</div>
</body>
</html>
```